Corporate Travel Technology Company needs new Business Card design

We need a new business card design to reflect our re-branded company. Our company is called tolvEn (pronounced tolvenn) and we provide Business Intelligence and mobile travel management solutions for the corporate travel industry. Our multinational customers use our solutions to manage large travel budgets and frequent travellers, as well as to save money and reduce risk. We'd like to see designs that use the blue and green palette as well as our corporate logo (attached below). The design should communicate innovation, insight, forward thinking, contemporary, trusted.

Target Market(s)

Large multinational corporates and Travel Agencies.

Industry/Entity Type

Business

Contact Information for Business Card

Rosalind Mercer
Chief Executive
tolvEn
Phone number - +61 (0)2 8134 2907
Email address - rosalind.mercer@tolven-example.com
Mobile number - +61 (0)438 516 702
www.tolven-example.com

Font styles to use
Other font styles liked:
• Please use font as close to corporate logo as possible

Colors
0255a3
0393ce
00a990
33b8a4
33a6d7
3176b5

Requirements
Must have
• Please include the words;
• Mobile Travel Management
• Accelerating Travel Business Insights
• Use corporate logo - although icon can be stylised if needed

```html
<!DOCTYPE html>
<html lang="en">
<head>
<meta charset="utf-8">
<title>tolvEn business card</title>
<link rel="stylesheet" href="https://fonts.googleapis.com/css2?family=Open+Sans:wght@400;600&family=Varela+Round&display=swap">
<style>
  :root {
    --page: #eceff1;
    --card-white: #f7f8f8;
    --brand-blue: #2a9fd6;
    --band-blue: #33a6d7;
    --brand-green: #00a990;
    --band-green: #33b8a4;
    --slate: #48595a;
    --ink-light: #ffffff;
    --ink-soft: #e3e9ea;
  }
  * { margin: 0; padding: 0; box-sizing: border-box; }
  html, body { width: 1200px; height: 902px; overflow: hidden; background: var(--page); }
  .canvas {
    width: 1200px; height: 902px;
    display: flex; flex-direction: column; align-items: center; justify-content: center; gap: 60px;
  }
  .card {
    position: relative; width: 620px; height: 354px; overflow: hidden;
    box-shadow: 0 6px 18px rgba(0,0,0,0.15);
  }
  .card-back {
    background: var(--brand-blue);
    display: flex; flex-direction: column; align-items: center; justify-content: center; gap: 18px;
  }
  .card-back::after {
    content: ""; position: absolute; left: 0; right: 0; bottom: 0; height: 10px; background: var(--band-green);
  }
  .card-front { background: var(--card-white); }
  .wave { position: absolute; inset: 0; }
  .brand {
    display: flex; align-items: center; gap: 14px;
    font-family: "Varela Round", sans-serif; color: var(--slate); line-height: 1;
  }
  .brand-dot { border-radius: 50%; background: var(--slate); }
  .card-back .brand { font-size: 104px; }
  .card-back .brand-dot { width: 44px; height: 44px; }
  .back-tagline {
    font-family: "Open Sans", sans-serif; font-size: 20px; color: var(--ink-light); letter-spacing: 0.5px;
  }
  .card-front .brand { position: absolute; left: 196px; top: 52px; font-size: 62px; gap: 10px; }
  .card-front .brand-dot { width: 24px; height: 24px; background: var(--band-blue); }
  .front-tagline {
    position: absolute; left: 232px; top: 126px;
    font-family: "Open Sans", sans-serif; font-size: 15px; font-weight: 600; color: var(--brand-green);
  }
  .holder {
    position: absolute; left: 28px; bottom: 26px;
    font-family: "Open Sans", sans-serif; color: var(--ink-light);
  }
  .holder-name { font-size: 27px; font-weight: 600; line-height: 1.15; }
  .holder-role { font-size: 20px; color: var(--ink-soft); }
  .contacts {
    position: absolute; right: 16px; top: 214px;
    border-left: 1px solid var(--ink-soft); padding-left: 10px;
    list-style: none; font-family: "Open Sans", sans-serif; font-size: 13.5px; color: var(--ink-light);
  }
  .contacts li { display: flex; align-items: center; gap: 10px; height: 24px; }
  .contacts svg { width: 14px; height: 14px; flex: none; }
</style>
</head>
<body>
<main class="canvas">
  <section class="card card-back" aria-label="Card back">
    <div class="brand"><span class="brand-dot"></span><span class="brand-name">tolvEn</span></div>
    <p class="back-tagline">Accelerating Travel Business Insights</p>
  </section>

  <section class="card card-front" aria-label="Card front">
    <svg class="wave" viewBox="0 0 620 354" preserveAspectRatio="none" aria-hidden="true">
      <path fill="var(--band-blue)" d="M0,236 C150,286 300,246 420,156 C490,106 560,96 620,86 L620,354 L0,354 Z"/>
      <path fill="var(--slate)" d="M0,252 C150,302 300,262 420,172 C490,122 560,112 620,102 L620,354 L0,354 Z"/>
    </svg>

    <div class="brand"><span class="brand-dot"></span><span class="brand-name">tolvEn</span></div>
    <p class="front-tagline">Mobile Travel Management</p>

    <div class="holder">
      <p class="holder-name">Rosalind Mercer</p>
      <p class="holder-role">Chief Executive</p>
    </div>

    <ul class="contacts">
      <li>
        <svg viewBox="0 0 14 14" aria-hidden="true"><rect x="0.5" y="0.5" width="13" height="13" rx="2" fill="none" stroke="#fff"/><rect x="3" y="6" width="8" height="5" fill="#fff"/><path d="M3,5 Q7,2 11,5" stroke="#fff" fill="none"/></svg>
        <span>+61 (0)2 8134 2907</span>
      </li>
      <li>
        <svg viewBox="0 0 14 14" aria-hidden="true"><rect x="0.5" y="0.5" width="13" height="13" rx="2" fill="none" stroke="#fff"/><rect x="5" y="3" width="4" height="8" rx="1" fill="#fff"/></svg>
        <span>+61 (0)438 516 702</span>
      </li>
      <li>
        <svg viewBox="0 0 14 14" aria-hidden="true"><rect x="0.5" y="0.5" width="13" height="13" rx="2" fill="none" stroke="#fff"/><circle cx="7" cy="7" r="4" fill="none" stroke="#fff"/><path d="M3,7 H11 M7,3 V11" stroke="#fff"/></svg>
        <span>www.tolven-example.com</span>
      </li>
      <li>
        <svg viewBox="0 0 14 14" aria-hidden="true"><rect x="0.5" y="0.5" width="13" height="13" rx="2" fill="none" stroke="#fff"/><rect x="3" y="4" width="8" height="6" fill="none" stroke="#fff"/><path d="M3,4 L7,7.5 L11,4" stroke="#fff" fill="none"/></svg>
        <span>rosalind.mercer@tolven-example.com</span>
      </li>
    </ul>
  </section>
</main>
</body>
</html>
```